Breakfast Cafe - The Sunny Nook

It is for my breakfast and lunch cafe with a hawaiian / beach theme. I am open 7 days a week from 7am to 2pm. We serve traditional American food such as omelettes, pancakes, burgers and sandwiches. I'll upload my old card and my new logo to be used. We have a lot of day to day regulars who eat there during the week, our t-shirts actually say 'Locals Only' on them. Hope this helps. Thanks.

Target Market(s)

anyone who has an appetite!

Industry/Entity Type

American Restaurant

Contact Information for Business Card

4815C Marlow Grove Avenue
Long Beach, California
(555) 731-2294

Requirements
Must have
• Address and phone number easily readable.
Nice to have
• beach or tropical theme

```html
<!DOCTYPE html>
<html lang="en">
<head>
<meta charset="utf-8">
<title>The Sunny Nook – Business Card</title>
<link href="https://fonts.googleapis.com/css2?family=Roboto:wght@400;700;900&display=swap" rel="stylesheet">
<style>
  :root {
    --stage: #3b3b3b;
    --card-dark: #0c0c0c;
    --card-light: #eeeeee;
    --ink: #111111;
    --muted: #6f6f6f;
    --emblem: #8a8a8a;
    --emblem-edge: #5a5a5a;
    --shadow: rgba(0, 0, 0, 0.45);
  }
  * { box-sizing: border-box; margin: 0; padding: 0; }
  html, body {
    width: 1200px;
    height: 900px;
    overflow: hidden;
    background: var(--stage);
    font-family: "Roboto", Arial, sans-serif;
  }
  .stage {
    width: 1200px;
    height: 900px;
    display: flex;
    flex-direction: column;
    align-items: center;
    justify-content: center;
    gap: 48px;
  }
  .card {
    width: 560px;
    height: 320px;
    border-radius: 26px;
    box-shadow: 0 10px 28px var(--shadow);
    display: flex;
    flex-direction: column;
    align-items: center;
    justify-content: center;
    text-align: center;
  }
  .card--back {
    background: var(--card-dark);
    color: var(--muted);
  }
  .card--front {
    background: var(--card-light);
    color: var(--ink);
  }
  .emblem {
    width: 130px;
    height: 130px;
    border-radius: 50%;
    background: radial-gradient(circle at 50% 45%, #b5b5b5, var(--emblem) 60%, var(--emblem-edge));
    margin-bottom: 14px;
  }
  .brand-name {
    font-weight: 900;
    font-size: 34px;
    letter-spacing: 1px;
    line-height: 1;
  }
  .card--back .brand-name { color: #9a9a9a; }
  .brand-place {
    font-weight: 700;
    font-size: 11px;
    letter-spacing: 5px;
    margin-top: 6px;
  }
  .card--back .brand-place { color: #8a8a8a; }
  .menu-line {
    font-size: 16px;
    margin-top: 24px;
    color: var(--muted);
  }
  .address {
    font-size: 17px;
    line-height: 1.2;
    margin-top: 8px;
  }
  .phone {
    font-weight: 700;
    font-size: 21px;
    margin-top: 16px;
  }
  .tagline {
    font-size: 18px;
    margin-top: 22px;
  }
  .hours {
    font-weight: 700;
    font-size: 21px;
    margin-top: 12px;
  }
</style>
</head>
<body>
  <main class="stage">
    <section class="card card--back">
      <div class="emblem" role="img" aria-label="Round beach scene emblem with palm tree and ocean"></div>
      <p class="brand-name">The Sunny Nook</p>
      <p class="brand-place">LONG BEACH, CA</p>
      <p class="menu-line">Omelettes | Pancakes | Burgers | Sandwiches</p>
    </section>

    <section class="card card--front">
      <p class="brand-name">The Sunny Nook</p>
      <p class="brand-place">LONG BEACH, CA</p>
      <p class="address">4815C Marlow Grove Avenue<br>Long Beach, California</p>
      <p class="phone">Phone: (555) 731-2294</p>
      <p class="tagline">Family owned and operated!</p>
      <p class="hours">Breakfast &amp; Lunch 7am - 2pm Daily</p>
    </section>
  </main>
</body>
</html>
```